Tavrelun Capital LLC

Need Professional Business cards for New Investment Fund

Target Market(s)

High Quality investors

Industry/Entity Type

Financial

Contact Information for Business Card

Phone Number +1 555 284 6190
Name Lukas Varenko
Title Fund Manager
email lv@FundTavrelun.com
Website www.FundTavrelun.com

Colors

Designer to choose colors to be used in the design.

Requirements
Must have
• Must have our Logo and all of the above. Must be made so lettering and loge can be raised

```html
<!DOCTYPE html>
<html lang="en">
<head>
<meta charset="utf-8">
<title>Tavrelun Capital – Business Card</title>
<link href="https://fonts.googleapis.com/css2?family=Raleway:wght@500;600&family=Teko:wght@500&display=swap" rel="stylesheet">
<style>
  :root {
    --stage: #1c1d1f;
    --front-bg: #434e42;
    --back-bg: #121417;
    --green: #5cbf4a;
    --muted-green: #3e4a3d;
    --white: #ffffff;
  }
  * { margin: 0; padding: 0; box-sizing: border-box; }
  html, body {
    width: 1200px; height: 900px; overflow: hidden;
    background: var(--stage);
    font-family: "Raleway", sans-serif;
  }
  .card {
    position: absolute; left: 250px;
    width: 700px; height: 400px;
    overflow: hidden;
  }
  /* Front */
  .card--front { top: 30px; background: var(--front-bg); }
  .brand {
    position: absolute; left: 0; right: 0; top: 170px;
    display: flex; align-items: center; justify-content: center; gap: 14px;
  }
  .brand__mark { width: 26px; height: 26px; background: var(--green); flex: none; }
  .brand__name {
    color: var(--white); font-weight: 600; font-size: 38px;
    letter-spacing: 4px; line-height: 1;
  }
  .front-bar {
    position: absolute; bottom: 0; left: 232px;
    width: 230px; height: 9px; background: var(--green);
  }
  /* Back */
  .card--back { top: 470px; background: var(--back-bg); }
  .identity {
    position: absolute; left: 40px; top: 250px; width: 222px; text-align: right;
  }
  .identity__name {
    font-family: "Teko", sans-serif; font-weight: 500;
    color: var(--white); font-size: 38px; line-height: 1;
    text-transform: uppercase; letter-spacing: 0.5px;
  }
  .identity__title {
    color: var(--white); font-size: 19px; font-weight: 500; margin-top: 4px;
  }
  .divider {
    position: absolute; left: 282px; top: 244px;
    width: 2px; height: 90px; background: var(--green);
  }
  .contacts {
    position: absolute; left: 304px; top: 244px;
    list-style: none;
  }
  .contacts__item {
    display: flex; align-items: center; gap: 12px;
    color: var(--white); font-size: 20px; font-weight: 500;
    height: 30px; white-space: nowrap;
  }
  .contacts__icon { width: 16px; height: 16px; flex: none; }
  .back-bar {
    position: absolute; bottom: 0; height: 10px;
  }
  .back-bar--accent { left: 0; width: 300px; background: var(--green); }
  .back-bar--muted { left: 308px; right: 0; background: var(--muted-green); }
</style>
</head>
<body>
  <section class="card card--front">
    <div class="brand">
      <span class="brand__mark"></span>
      <span class="brand__name">TAVRELUN</span>
    </div>
    <div class="front-bar"></div>
  </section>

  <section class="card card--back">
    <div class="identity">
      <div class="identity__name">Lukas Varenko</div>
      <div class="identity__title">Title Fund Manager</div>
    </div>
    <div class="divider"></div>
    <ul class="contacts">
      <li class="contacts__item">
        <svg class="contacts__icon" viewBox="0 0 16 16" aria-hidden="true">
          <path d="M4 1.5l2.2 3-1.3 1.6c.8 1.8 2.2 3.2 4 4l1.6-1.3 3 2.2-1.2 2.5C7 13.3 2.7 9 1.5 2.7z" fill="var(--green)"/>
        </svg>
        +1 555 284 6190
      </li>
      <li class="contacts__item">
        <svg class="contacts__icon" viewBox="0 0 16 16" aria-hidden="true">
          <rect x="1.5" y="3.5" width="13" height="9" fill="none" stroke="var(--green)" stroke-width="1.4"/>
          <path d="M1.5 3.5l6.5 5 6.5-5" fill="none" stroke="var(--green)" stroke-width="1.4"/>
        </svg>
        lv@FundTavrelun.com
      </li>
      <li class="contacts__item">
        <svg class="contacts__icon" viewBox="0 0 16 16" aria-hidden="true">
          <g fill="none" stroke="var(--green)" stroke-width="1.2">
            <circle cx="8" cy="8" r="6.5"/>
            <ellipse cx="8" cy="8" rx="3" ry="6.5"/>
            <path d="M1.5 8h13M2.5 4.8h11M2.5 11.2h11"/>
          </g>
        </svg>
        www.FundTavrelun.com
      </li>
    </ul>
    <div class="back-bar back-bar--accent"></div>
    <div class="back-bar back-bar--muted"></div>
  </section>
</body>
</html>
```